Label Design for 2x Chutney Products

We need a label design for 2x Chutney Products.
Marigo Chutney - Red Chili
Marigo Chutney - Green Chili & Coriander
See attached pictures. This is just sample pictures so you get an impression of the product and the colors. Both labels to have as title the generic name "Marigo Chutney" and then added either Red Chili or Green Chili & Coriander. The different terms needs to be good readable and can differ in font/color/size, or in the same style if this makes more sense from design point (as I am not a designer). The labels later on need to be editable in the way that the ingredient list, nutrition list, basis company and production information can be added. If this needs to be done directly and cannot be edited later on please let know. Editable design related the additional text also would be good as the additional information need to be added in different languages (Dutch. German and perhaps French). No clue how this is to be implemented but looking forward to receive some input/solutions on this.
I already had a project to create the company logo. I consider this logo to be used as the product logo and not the company logo. A different company logo later on can be designed from new. This logo is here attached. Either to work with this logo and use it as product logo (perhaps revise the colors) and add the product description or create a new logo for the product from scratch if you feel too. The logo itself should be easily readable for the product name/description and the colors appealing to such product and of course customers.
Please contact if any clarification needed. Thanks in advance for your efforts and ideas for this project.

Industry/Entity Type

Food

Font styles to use
Other font styles liked:
• Asian Touch

Requirements
Nice to have
• If possible "simply" editable for text fields in order to add/revise the ingredient list, nutrition list, revise to different languages.

```html
<!DOCTYPE html>
<html lang="en">
<head>
<meta charset="utf-8">
<title>Marigo Chutney – Label Set</title>
<link href="https://fonts.googleapis.com/css2?family=Rammetto+One&family=Oswald:wght@400;500&display=swap" rel="stylesheet">
<style>
  :root {
    --backdrop: #f6b91f;
    --red-label: #e9434a;
    --red-label-deep: #d9373f;
    --green-label: #6aa83a;
    --green-label-deep: #5e9a33;
    --cream: #f3cd4f;
    --cream-soft: rgba(243, 205, 79, 0.85);
    --rule: rgba(243, 205, 79, 0.7);
  }
  * { margin: 0; padding: 0; box-sizing: border-box; }
  html, body { width: 1200px; height: 1200px; overflow: hidden; }
  body {
    background: var(--backdrop);
    font-family: "Oswald", sans-serif;
    position: relative;
  }
  .label {
    position: absolute;
    left: 140px;
    width: 920px;
    height: 400px;
    color: var(--cream);
  }
  .label--red { top: 150px; background: linear-gradient(100deg, var(--red-label-deep), var(--red-label)); }
  .label--green { top: 650px; background: linear-gradient(100deg, var(--green-label-deep), var(--green-label)); }

  .label__frame {
    position: absolute;
    inset: 22px 18px;
    border-top: 2px solid var(--rule);
    border-bottom: 2px solid var(--rule);
  }

  .brand {
    position: absolute;
    left: 30px;
    top: 112px;
    width: 60px;
    display: flex;
    flex-direction: column;
    align-items: center;
    gap: 10px;
  }
  .brand__dot {
    width: 44px; height: 44px;
    border-radius: 50%;
    background: var(--cream-soft);
  }
  .brand__name {
    font-family: "Oswald", sans-serif;
    font-weight: 500;
    font-size: 14px;
    line-height: 1.05;
    text-align: center;
    letter-spacing: 1px;
    text-transform: uppercase;
    color: var(--cream-soft);
  }

  .title {
    position: absolute;
    left: 100px;
    top: 62px;
    font-family: "Rammetto One", serif;
    font-size: 92px;
    line-height: 0.92;
    letter-spacing: -2px;
    color: var(--cream);
  }
  .title__line { display: block; white-space: nowrap; }
  .title__line--second { margin-left: 4px; }

  .chili-icon {
    position: absolute;
    left: 690px;
    top: 60px;
    width: 38px;
    height: 84px;
    border-radius: 20px 20px 30px 6px;
    background: #fbf4e0;
    transform: rotate(28deg);
  }

  .flavour {
    position: absolute;
    left: 102px;
    top: 286px;
    display: flex;
    align-items: center;
    gap: 16px;
    font-family: "Oswald", sans-serif;
    font-size: 24px;
    letter-spacing: 6px;
    text-transform: uppercase;
    color: var(--cream-soft);
  }
  .flavour__hatch { letter-spacing: 4px; opacity: 0.9; }

  .weight {
    position: absolute;
    right: 128px;
    top: 270px;
    display: flex;
    align-items: center;
    gap: 6px;
  }
  .weight__rule { width: 30px; height: 2px; background: var(--rule); }
  .weight__badge {
    width: 54px; height: 54px;
    border-radius: 50%;
    background: var(--cream);
    color: var(--red-label-deep);
    font-family: "Oswald", sans-serif;
    font-weight: 500;
    font-size: 15px;
    display: flex; align-items: center; justify-content: center;
  }
  .label--green .weight__badge { color: var(--green-label-deep); }

  .facts {
    position: absolute;
    right: 28px;
    top: 60px;
    width: 80px;
    height: 280px;
    border-left: 2px solid var(--rule);
    display: flex;
    flex-direction: column;
  }
  .facts__cell {
    flex: 1;
    border-bottom: 2px solid var(--rule);
    display: flex;
    flex-direction: column;
    align-items: center;
    justify-content: center;
    gap: 6px;
    color: var(--cream-soft);
  }
  .facts__cell:last-child { border-bottom: none; }
  .facts__value { font-size: 34px; font-weight: 500; line-height: 1; }
  .facts__note { font-size: 11px; letter-spacing: 1.5px; text-transform: uppercase; }
  .facts__mark {
    width: 26px; height: 26px;
    border-radius: 6px;
    background: rgba(243, 205, 79, 0.55);
  }
</style>
</head>
<body>

  <section class="label label--red">
    <div class="label__frame"></div>
    <div class="brand">
      <span class="brand__dot"></span>
      <span class="brand__name">Saffra<br>Foods</span>
    </div>
    <h1 class="title">
      <span class="title__line">Marigo</span>
      <span class="title__line title__line--second">Chutney</span>
    </h1>
    <div class="chili-icon" role="img" aria-label="Small chili pepper icon"></div>
    <p class="flavour"><span>Red Chili</span><span class="flavour__hatch">///////////////////</span></p>
    <div class="weight"><span class="weight__rule"></span><span class="weight__badge">100 gr</span></div>
    <div class="facts">
      <div class="facts__cell"><span class="facts__value">36</span><span class="facts__note">Calories</span></div>
      <div class="facts__cell"><span class="facts__mark" role="img" aria-label="Leaf icon"></span><span class="facts__note">Vegan</span></div>
      <div class="facts__cell"><span class="facts__mark" role="img" aria-label="Chili icon"></span><span class="facts__note">Spicy</span></div>
    </div>
  </section>

  <section class="label label--green">
    <div class="label__frame"></div>
    <div class="brand">
      <span class="brand__dot"></span>
      <span class="brand__name">Saffra<br>Foods</span>
    </div>
    <h1 class="title">
      <span class="title__line">Marigo</span>
      <span class="title__line title__line--second">Chutney</span>
    </h1>
    <div class="chili-icon" role="img" aria-label="Small chili pepper icon"></div>
    <p class="flavour"><span>Green Chili &amp; Coriander</span><span class="flavour__hatch">/////////</span></p>
    <div class="weight"><span class="weight__rule"></span><span class="weight__badge">100 gr</span></div>
    <div class="facts">
      <div class="facts__cell"><span class="facts__value">36</span><span class="facts__note">Calories</span></div>
      <div class="facts__cell"><span class="facts__mark" role="img" aria-label="Leaf icon"></span><span class="facts__note">Vegan</span></div>
      <div class="facts__cell"><span class="facts__mark" role="img" aria-label="Chili icon"></span><span class="facts__note">Spicy</span></div>
    </div>
  </section>

</body>
</html>
```